Business Card Design for Property Development Company Director

I am looking for a professional and unforgettable business card design for our Director of our Property Development Company.
Please see attached .pptx file to find out what information to include. You don't have to follow the exact format shown in the file - I am interested to see your creative flair using the information provided.

```html
<!DOCTYPE html>
<html lang="en">
<head>
<meta charset="utf-8">
<title>Halvard Property Group – Business Cards</title>
<link href="https://fonts.googleapis.com/css2?family=Roboto:wght@400;500;700&family=Roboto+Condensed:wght@700&display=swap" rel="stylesheet">
<style>
  :root {
    --bg: #e6e7e9;
    --card: #f7f7f8;
    --navy: #22448e;
    --grey: #5c5e62;
    --text-grey: #4a4c50;
    --white: #ffffff;
  }
  * { margin: 0; padding: 0; box-sizing: border-box; }
  html, body {
    width: 1200px; height: 726px; overflow: hidden;
    background: var(--bg);
    font-family: "Roboto", Arial, sans-serif;
  }
  .stage { position: relative; width: 1200px; height: 726px; }

  .card {
    position: absolute;
    width: 540px; height: 308px;
    background: var(--card);
    box-shadow: 0 6px 18px rgba(0,0,0,0.12);
    overflow: hidden;
  }
  .card--front { left: 50px; top: 70px; }
  .card--back  { left: 610px; top: 348px; }

  /* Brand stand-in */
  .brand { display: flex; align-items: center; gap: 12px; }
  .brand__mark { width: 30px; height: 30px; background: var(--grey); flex: none; }
  .brand__name {
    font-weight: 700; color: var(--navy);
    font-size: 30px; line-height: 1.05; letter-spacing: 0.5px;
    text-transform: uppercase;
  }

  /* Front */
  .front__tagline {
    position: absolute; top: 30px; right: 40px;
    text-align: center; color: var(--navy);
    font-size: 18px; line-height: 1.2;
  }
  .front__brand { position: absolute; top: 108px; left: 66px; }
  .front__stripe {
    position: absolute; top: 196px; left: 0; width: 540px; height: 10px;
    display: flex;
  }
  .front__stripe .seg-grey { width: 52%; background: var(--grey); }
  .front__stripe .seg-navy { flex: 1; background: var(--navy); }
  .front__invite {
    position: absolute; top: 222px; left: 40px; right: 30px;
    color: var(--text-grey); font-size: 15px;
  }
  .front__invite .accent { color: var(--navy); }

  /* Back */
  .back__wave { position: absolute; inset: 0; }
  .back__person { position: absolute; top: 14px; right: 30px; text-align: right; }
  .back__name {
    font-family: "Roboto Condensed", "Roboto", sans-serif;
    font-weight: 700; color: var(--navy); font-size: 20px; line-height: 24px;
  }
  .back__role { color: var(--text-grey); font-size: 12px; line-height: 15px; }
  .back__brand { position: absolute; top: 96px; left: 40px; }
  .back__brand .brand__name { font-size: 22px; }

  .contacts {
    position: absolute; top: 146px; right: 24px;
    list-style: none; text-align: right;
    color: var(--white); font-size: 13px; line-height: 21px;
  }
  .contacts li { display: flex; justify-content: flex-end; align-items: center; gap: 7px; }
  .contacts svg { width: 12px; height: 12px; flex: none; }
  .contacts .licence { padding-right: 19px; }
</style>
</head>
<body>
<main class="stage">

  <section class="card card--front" aria-label="Business card front">
    <p class="front__tagline">Property Development<br>&amp; Site Acquisition Specialists</p>
    <div class="brand front__brand">
      <span class="brand__mark"></span>
      <span class="brand__name">Halvard Property Group</span>
    </div>
    <div class="front__stripe"><span class="seg-grey"></span><span class="seg-navy"></span></div>
    <p class="front__invite">Ask me about our <span class="accent">INVESTMENT &amp; PARTNERSHIP</span> opportunities</p>
  </section>

  <section class="card card--back" aria-label="Business card back">
    <svg class="back__wave" viewBox="0 0 540 308" aria-hidden="true">
      <path d="M540,82 C435,84 385,112 345,152 C305,192 275,225 225,252 C175,276 100,284 0,286 L0,308 L540,308 Z" fill="var(--navy)"/>
      <path d="M540,66 C425,68 370,96 330,136 C290,176 262,208 212,236 C160,262 95,270 0,272" fill="none" stroke="var(--grey)" stroke-width="8"/>
      <path d="M0,299 C110,299 185,294 240,280" fill="none" stroke="var(--grey)" stroke-width="5"/>
    </svg>

    <div class="back__person">
      <p class="back__name">Daniel Marsh</p>
      <p class="back__role">Director</p>
    </div>

    <div class="brand back__brand">
      <span class="brand__mark"></span>
      <span class="brand__name">Halvard<br>Property Group</span>
    </div>

    <ul class="contacts">
      <li>0400 218 736
        <svg viewBox="0 0 12 12" aria-hidden="true"><path d="M3 1 L5 3.5 L4 5 C4.8 6.6 5.6 7.4 7 8 L8.5 7 L11 9 L10 11 C5 11 1 7 1 2 Z" fill="var(--white)"/></svg>
      </li>
      <li>www.halvardgroup.com.au
        <svg viewBox="0 0 12 12" aria-hidden="true"><circle cx="6" cy="6" r="5" fill="none" stroke="var(--white)" stroke-width="1.2"/><path d="M1 6 H11 M6 1 C3.5 4 3.5 8 6 11 M6 1 C8.5 4 8.5 8 6 11" fill="none" stroke="var(--white)" stroke-width="1"/></svg>
      </li>
      <li>daniel@halvardgroup.com.au
        <svg viewBox="0 0 12 12" aria-hidden="true"><rect x="0.8" y="2.5" width="10.4" height="7" fill="none" stroke="var(--white)" stroke-width="1.2"/><path d="M1 3 L6 7 L11 3" fill="none" stroke="var(--white)" stroke-width="1.2"/></svg>
      </li>
      <li class="licence">Real Estate Lic: 5172093 &amp; 5172094</li>
    </ul>
  </section>

</main>
</body>
</html>
```